Ridgeline Orchards Organic Cherry POS card 7x11

We are wanting to create a one-sided 7 x 11 organic cherry card that is eye catching and informative.This should be clear and easy to read and not cluttered. We use these cards as a display in grocery stores, demo stands, and other events to market Organic Ridgeline Sweet Orchards. We have a few facts that we would like displayed on the card (see attachment).

Target Market(s)

Consumers

Industry/Entity Type

Agriculture

Requirements
Must have
• Natural color palettes
• Easy to read
• Ridgeline Orchards
Nice to have
• Unique, realistic cherry design

```html
<!DOCTYPE html>
<html lang="en">
<head>
<meta charset="utf-8">
<title>Ridgeline Orchards – Organic Cherry Card</title>
<link rel="stylesheet" href="https://fonts.googleapis.com/css2?family=Josefin+Sans:wght@400;600&family=Kaushan+Script&display=swap">
<style>
  :root {
    --paper: #ffffff;
    --cherry-maroon: #7d1a3c;
    --dash-maroon: #6a1c30;
    --leaf-green: #6b8f1c;
    --wash-green: #d8f3b4;
    --wash-green-soft: #ecfadc;
    --cherry-red: #c8101c;
    --cherry-deep: #7e0810;
    --brand-dot: #2f8a4e;
  }
  * { margin: 0; padding: 0; box-sizing: border-box; }
  html, body { width: 1200px; height: 880px; overflow: hidden; background: var(--paper); }
  .card {
    position: relative;
    width: 1200px;
    height: 880px;
    background: var(--paper);
    overflow: hidden;
    font-family: "Josefin Sans", sans-serif;
  }
  .wash {
    position: absolute;
    left: 0; top: 56px;
    width: 1200px; height: 768px;
    background:
      radial-gradient(ellipse 340px 260px at 900px 200px, var(--wash-green) 0%, rgba(216,243,180,0) 100%),
      radial-gradient(ellipse 300px 280px at 220px 620px, var(--wash-green) 0%, rgba(216,243,180,0) 100%),
      radial-gradient(ellipse 420px 300px at 760px 560px, var(--wash-green-soft) 0%, rgba(236,250,220,0) 100%),
      radial-gradient(ellipse 260px 200px at 520px 420px, var(--wash-green-soft) 0%, rgba(236,250,220,0) 100%);
  }
  .brand {
    position: absolute;
    left: 48px; top: 118px;
    display: flex;
    align-items: center;
    gap: 18px;
  }
  .brand-dot {
    width: 56px; height: 56px;
    border-radius: 50%;
    background: var(--brand-dot);
  }
  .brand-name {
    font-size: 46px;
    font-weight: 600;
    color: var(--cherry-maroon);
    letter-spacing: 0.02em;
  }
  .facts {
    position: absolute;
    left: 0; top: 0;
    width: 624px;
    height: 880px;
    color: var(--cherry-maroon);
    font-size: 31px;
    font-weight: 400;
    letter-spacing: 0.3em;
    text-transform: uppercase;
  }
  .facts p {
    position: absolute;
    left: 0; width: 100%;
    text-align: center;
    line-height: 1;
    padding-left: 0.3em;
  }
  .cherries {
    position: absolute;
    left: 660px; top: 200px;
    width: 440px; height: 320px;
    border-radius: 50%;
    background: radial-gradient(ellipse at 40% 35%, var(--cherry-red) 0%, #b00d18 55%, var(--cherry-deep) 100%);
  }
  .dashes {
    position: absolute;
    left: 0; top: 0;
    width: 1200px; height: 880px;
    pointer-events: none;
  }
  .benefits {
    position: absolute;
    left: 654px; top: 578px;
    width: 440px;
    text-align: center;
    font-family: "Kaushan Script", cursive;
    color: var(--leaf-green);
    font-size: 30px;
    line-height: 33px;
  }
</style>
</head>
<body>
  <main class="card">
    <div class="wash" role="img" aria-label="Soft green watercolour wash across the background"></div>

    <div class="brand">
      <span class="brand-dot"></span>
      <span class="brand-name">Ridgeline Orchards</span>
    </div>

    <section class="facts">
      <p style="top:272px">Organic</p>
      <p style="top:316px">Ridgeline Orchards</p>
      <p style="top:374px">Make up 1/3</p>
      <p style="top:432px">of the nation's</p>
      <p style="top:476px">production.</p>
      <p style="top:558px">Washington State</p>
      <p style="top:602px">is the nation's</p>
      <p style="top:646px">largest producer</p>
      <p style="top:690px">of organic</p>
      <p style="top:734px">cherries.</p>
    </section>

    <div class="cherries" role="img" aria-label="Photograph of a bunch of ripe red sweet cherries with green stems"></div>

    <svg class="dashes" viewBox="0 0 1200 880" aria-hidden="true">
      <g fill="none" stroke="var(--dash-maroon)" stroke-width="6" stroke-dasharray="26 16">
        <path d="M 1039 494 A 250 222 0 1 1 1088 440" />
        <path d="M 1048 500 Q 1100 580 1030 660" />
      </g>
    </svg>

    <section class="benefits">
      <p>Health benefits:</p>
      <p>Fat Free</p>
      <p>Source of Vitamin C</p>
      <p>A Natural Anti-Inflammatory</p>
      <p>Source of Potassium</p>
      <p>Source of Melatonin</p>
    </section>
  </main>
</body>
</html>
```